Agriculture Business Card

I want to use my existing logo and use my tagline of "Don't Guess...Soil Test" on the card. Looking for a double sided card that will really get peoples attention.
Contact Info:
Marlow Field Crop Edge
Calvin Brusk
2917 K Lane
Larkin, NE 68593
402-555-0193
calvin.r.brusk@fieldmailbox.net

```html
<!DOCTYPE html>
<html lang="en">
<head>
<meta charset="utf-8">
<title>Marlow Field Crop Edge – Business Card</title>
<link href="https://fonts.googleapis.com/css2?family=Montserrat:wght@400;500;600&display=swap" rel="stylesheet">
<style>
  :root {
    --stage: #d9d9d6;
    --card-white: #ffffff;
    --card-soil: #a0684c;
    --soil-dark: #8a5640;
    --name-green: #3aa845;
    --text-grey: #5a5a5a;
    --accent-gold: #f2b01e;
    --brand-brown: #8a5a44;
    --rule: #c9a996;
  }
  * { box-sizing: border-box; margin: 0; padding: 0; }
  html, body { width: 1200px; height: 801px; overflow: hidden; }
  body {
    background: var(--stage);
    font-family: "Montserrat", sans-serif;
    display: flex;
    align-items: center;
    justify-content: center;
    gap: 40px;
  }
  .card {
    width: 540px;
    height: 309px;
    position: relative;
    box-shadow: 0 6px 18px rgba(0,0,0,0.15);
  }
  .card--front { background: var(--card-white); }
  .card--back { background: var(--card-soil); }

  .brand {
    position: absolute;
    left: 40px;
    top: 0;
    bottom: 0;
    width: 200px;
    display: flex;
    align-items: center;
    gap: 10px;
  }
  .brand__dot {
    flex: none;
    width: 22px;
    height: 22px;
    border-radius: 50%;
    background: var(--accent-gold);
  }
  .brand__name {
    color: var(--brand-brown);
    font-weight: 600;
    font-size: 18px;
    line-height: 1.2;
  }
  .divider {
    position: absolute;
    left: 262px;
    top: 70px;
    width: 1px;
    height: 170px;
    background: linear-gradient(var(--rule), rgba(201,169,150,0.2));
  }
  .contact {
    position: absolute;
    left: 290px;
    top: 72px;
    color: var(--text-grey);
  }
  .contact__name {
    color: var(--name-green);
    font-weight: 600;
    font-size: 20px;
    letter-spacing: 0.5px;
    text-transform: uppercase;
    margin-bottom: 16px;
  }
  .contact__address {
    font-size: 13px;
    line-height: 1.5;
    margin-bottom: 14px;
  }
  .contact__line {
    display: flex;
    align-items: center;
    gap: 8px;
    font-size: 12.5px;
    line-height: 1.9;
  }
  .contact__icon { width: 12px; height: 12px; flex: none; }

  .back-mark {
    position: absolute;
    left: 40px;
    top: 40px;
    width: 300px;
    height: 229px;
    display: flex;
    align-items: center;
    gap: 12px;
  }
  .back-mark__dot {
    flex: none;
    width: 40px;
    height: 40px;
    border-radius: 50%;
    background: var(--soil-dark);
  }
  .back-mark__name {
    color: var(--soil-dark);
    font-weight: 600;
    font-size: 26px;
    line-height: 1.2;
  }
  .tagline {
    position: absolute;
    right: 34px;
    bottom: 40px;
    color: var(--accent-gold);
    font-size: 17px;
    font-weight: 500;
    letter-spacing: 0.5px;
  }
</style>
</head>
<body>
  <section class="card card--front">
    <div class="brand">
      <span class="brand__dot"></span>
      <span class="brand__name">Marlow Field Crop Edge</span>
    </div>
    <div class="divider"></div>
    <div class="contact">
      <h1 class="contact__name">Calvin Brusk</h1>
      <p class="contact__address">2917 K Lane<br>Larkin, NE 68593</p>
      <p class="contact__line">
        <svg class="contact__icon" viewBox="0 0 24 24" aria-hidden="true"><path fill="#f2b01e" d="M6.6 10.8a15.1 15.1 0 0 0 6.6 6.6l2.2-2.2a1 1 0 0 1 1-.25 11.4 11.4 0 0 0 3.6.57 1 1 0 0 1 1 1V20a1 1 0 0 1-1 1A17 17 0 0 1 3 4a1 1 0 0 1 1-1h3.5a1 1 0 0 1 1 1c0 1.25.2 2.45.57 3.57a1 1 0 0 1-.25 1z"/></svg>
        402-555-0193
      </p>
      <p class="contact__line">
        <svg class="contact__icon" viewBox="0 0 24 24" aria-hidden="true"><path fill="#f2b01e" d="M2 5h20v14H2z"/><path fill="none" stroke="#fff" stroke-width="2" d="M3 6l9 7 9-7"/></svg>
        calvin.r.brusk@fieldmailbox.net
      </p>
    </div>
  </section>

  <section class="card card--back">
    <div class="back-mark">
      <span class="back-mark__dot"></span>
      <span class="back-mark__name">Marlow Field Crop Edge</span>
    </div>
    <p class="tagline">Don't Guess...Soil Test</p>
  </section>
</body>
</html>
```